Institutional website for an IT Consulting company

Web design + HTML + CSS / Bootstrap + JS (interaction) integration in order to extend our existing website brightvale.coop.
Our website is currently aiming only for recruitment and not for customers, we want to provide a fluid transition between customer side website (this project) and recruitment website (existing site).

Ideally we would love the new design to be "inspired" by our actual graphic chart (Colors mainly). It should provide a great user experience and a landing page (or any mean) allowing the visitor to easily switch from the end customer front end (this project), the recruitment front end (existing front end https://www.brightvale.coop/) and the existing member front end (an other existing front end dedicated to members already existing).

In attachment you will find the expected site content mainly a one page with a first level of information and "link" to sub pages (a way to directly access this sub pages should also be provided).

The website should be accessible on mobile device and desktop.

The attachment is in french as it reflect the final site content, but if google translate isn't sufficient to have a general idea of the content, feel free to ask. We would love to have some visual representation for some categories.

Target Market(s)

fortune 500 companies

Industry/Entity Type

It Company

Coding

Coded - Design and coding required

Number of Pages Required

5+ page

Requirements
Must have
• This project must have an easy way to navigate between 3 sub sites, the customer one (the one designed here), the consultant / recruitment one (the existing one at brightvale.coop), the members one.

A one page experience at first leading to detail pages.

Custom made visuals to illustrate each categories.

Inspiration websites : pirog[.]fr ; tasklynn[.]com ; dorvelo[.] com ...

Be inspired by the existing color from our logo and existing website at brightvale[.]coop

```html
<!DOCTYPE html>
<html lang="en">
<head>
<meta charset="utf-8">
<title>Brightvale — Experts in their field</title>
<link href="https://fonts.googleapis.com/css2?family=Montserrat:wght@600;700;800&family=Lato:wght@400;700&family=Open+Sans:wght@400;600&display=swap" rel="stylesheet">
<style>
:root{
  --teal:#12b3bf;
  --teal-deep:#0ea6b2;
  --ink:#123c45;
  --dark:#333333;
  --text:#6b6b6b;
  --muted:#888888;
  --line:#d6d6d6;
  --white:#ffffff;
  --placeholder:#c9c9c9;
}
*{box-sizing:border-box;margin:0;padding:0}
html,body{width:1200px;height:3506px;overflow:hidden;background:var(--white)}
body{position:relative;font-family:"Lato",sans-serif;color:var(--text)}
.abs{position:absolute}

/* header */
.brand{display:flex;align-items:center;gap:12px;font-family:"Montserrat",sans-serif;font-weight:800;color:var(--ink);letter-spacing:1px}
.brand-mark{width:30px;height:30px;background:var(--teal)}
.site-header .brand{left:110px;top:33px;font-size:40px}
.util-links{right:112px;top:16px;font-family:"Montserrat",sans-serif;font-weight:600;font-size:15px;color:var(--dark);display:flex;gap:12px;align-items:center}
.util-links svg{vertical-align:-2px;margin-right:5px}
.nav-btn{top:50px;height:50px;border:2px solid #9a9a9a;font-family:"Montserrat",sans-serif;font-weight:600;font-size:15px;color:#555;display:flex;align-items:center;justify-content:center}
.nav-btn.primary{background:var(--dark);border-color:var(--dark);color:var(--white)}

/* hero */
.hero{left:0;top:122px;width:1200px;height:404px;background:linear-gradient(100deg,#3c3b3d 0%,#6d5a55 35%,#a59a90 55%,#55403f 80%,#7a4450 100%)}
.hero-title{left:82px;top:252px;font-family:"Montserrat",sans-serif;font-weight:700;color:var(--white);line-height:1.1}
.hero-title .small{font-size:50px;display:block}
.hero-title .big{font-size:68px;display:block;margin-top:8px}
.hero-dots{left:549px;top:465px;display:flex;gap:10px}
.hero-dots span{width:18px;height:18px;border-radius:50%;border:2px solid #ddd}
.hero-dots span.on{background:#ccc}

/* partners */
.badge{width:340px;height:340px;border-radius:50%;background:var(--white);box-shadow:0 4px 18px rgba(0,0,0,.16);display:flex;align-items:center;justify-content:center}
.badge-shape{width:200px;height:120px;border-radius:10px;background:#e9eef0}
.badge-shape.square{width:170px;height:170px;border-radius:6px}
.partner-text{font-size:14.5px;line-height:29px;color:var(--text)}

.team-lead{left:0;width:1200px;top:1560px;text-align:center;font-family:"Open Sans",sans-serif;font-size:25px;line-height:43px;color:#666}

/* team */
.portrait{width:369px;height:381px;background:var(--teal);padding:26px}
.portrait-inner{width:100%;height:100%;background:var(--white);padding:9px}
.portrait-img{width:100%;height:100%;background:var(--placeholder)}
.member-name{font-family:"Open Sans",sans-serif;font-size:33px;color:#666}
.member-bio{font-size:14.5px;line-height:27.5px;color:var(--text)}
.contact-line{font-family:"Open Sans",sans-serif;font-size:17px;color:#555;display:flex;align-items:center;gap:10px}

/* testimonials */
.testimonials{left:0;top:2587px;width:1200px;height:511px;background:linear-gradient(90deg,var(--teal-deep),var(--teal))}
.testimonials-title{left:0;width:1200px;top:55px;text-align:center;font-family:"Montserrat",sans-serif;font-weight:700;font-size:44px;color:var(--white)}
.client{top:171px;width:183px;height:87px;border:5px solid rgba(255,255,255,.45);display:flex;align-items:center;justify-content:center;gap:8px;font-family:"Montserrat",sans-serif;font-weight:700;font-size:30px;color:rgba(255,255,255,.6)}
.client .dot{width:16px;height:16px;background:rgba(255,255,255,.6)}
.client.active{border-color:var(--white);color:var(--white);background:transparent}
.client.active .dot{background:var(--white)}
.rule{left:110px;top:303px;width:978px;height:1px;background:rgba(255,255,255,.35)}
.avatar{left:109px;top:329px;width:120px;height:120px;border-radius:50%;background:linear-gradient(160deg,#e8e3df,#b9a79a)}
.author{left:258px;top:365px;font-family:"Open Sans",sans-serif;font-size:19px;line-height:31px;color:var(--white)}
.quote{left:386px;top:344px;width:702px;font-style:italic;font-size:17px;line-height:27px;color:var(--white)}

/* footer */
.site-footer .brand{left:110px;top:3226px;font-size:40px}
.foot-col h4{font-family:"Open Sans",sans-serif;font-weight:600;font-size:19px;color:#555;margin-bottom:10px}
.foot-col li{list-style:none;font-size:14.5px;line-height:26.7px;color:var(--muted)}
.find li{display:flex;gap:8px;align-items:flex-start}
.foot-rule{left:110px;top:3432px;width:978px;height:1px;background:var(--line)}
.copyright{left:110px;top:3460px;font-size:15px;color:var(--muted)}
.social{top:3450px;width:44px;height:44px;border-radius:50%;border:1.5px solid var(--teal);display:flex;align-items:center;justify-content:center}
.social span{width:8px;height:8px;border-radius:50%;background:var(--teal)}
</style>
</head>
<body>

<header class="site-header">
  <div class="brand abs"><span class="brand-mark"></span>BRIGHTVALE</div>
  <div class="util-links abs">
    <span><svg width="11" height="13" viewBox="0 0 11 13"><rect x="0" y="5" width="11" height="8" rx="1" fill="#12b3bf"/><path d="M2.5 5V3.5a3 3 0 0 1 6 0V5" stroke="#12b3bf" stroke-width="1.6" fill="none"/></svg>LOG IN</span>
    <span>|</span>
    <span><svg width="13" height="13" viewBox="0 0 13 13"><circle cx="6.5" cy="6.5" r="6.5" fill="#12b3bf"/><text x="6.5" y="10" font-size="9" text-anchor="middle" fill="#fff" font-family="Arial,sans-serif" font-weight="700">?</text></svg>HELP</span>
  </div>
  <a class="nav-btn abs" style="left:530px;width:150px">I AM BRIGHTVALE</a>
  <a class="nav-btn abs" style="left:697px;width:238px">I WISH TO JOIN BRIGHTVALE</a>
  <a class="nav-btn primary abs" style="left:955px;width:133px">CONTACT US</a>
</header>

<section class="hero abs" role="img" aria-label="Photo of consultants gathered around a meeting table with documents and a coffee mug"></section>
<h1 class="hero-title abs"><span class="small">EXPERTS IN</span><span class="big">THEIR FIELD</span></h1>
<div class="hero-dots abs"><span class="on"></span><span></span><span></span><span></span></div>

<section class="partners">
  <div class="badge abs" style="left:110px;top:568px"><div class="badge-shape" role="img" aria-label="Partner certification badge"></div></div>
  <p class="partner-text abs" style="left:500px;top:637px;width:590px">Combining junior experiences to more than 15 years of data projects in Corvane's environments, Brightvale is able to take over all the standard steps of a MOE project. With half certified consultants on 35 different certifications, Brightvale has a great added value on all data platform issues encountered in Corvane tools. Operational on cost-plus contracts for long-term missions as well as punctual audit contracts, we provide support to product deployment such as Chartwise.</p>

  <div class="badge abs" style="left:748px;top:850px"><div class="badge-shape square" role="img" aria-label="Training quality certification badge"></div></div>
  <p class="partner-text abs" style="left:110px;top:982px;width:580px">The Formacert agreements, and specially the recognition of CCT valuate our skills on training your staff and the funding opportunities of these trainings.</p>

  <div class="badge abs" style="left:110px;top:1158px"><div class="badge-shape" role="img" aria-label="Cloud solution provider badge"></div></div>
  <p class="partner-text abs" style="left:500px;top:1266px;width:590px">Last particular aspect, our reseller Corvane CSP status allows us to provide Corvane Office licences and Skyline consumption credit, while providing support in data deployment on these infrastructure. With a specific monitoring of your licences, whether you have 10 or 1 000 users, feel free to contact us on our CSP program</p>
</section>

<h2 class="team-lead abs">Our commercial and administrative team is also at your service, but also<br>to S/E in order to assist them on daily tasks.</h2>

<section class="team">
  <div class="portrait abs" style="left:112px;top:1683px"><div class="portrait-inner"><div class="portrait-img" role="img" aria-label="Portrait of Camille"></div></div></div>
  <h3 class="member-name abs" style="left:546px;top:1672px">Camille</h3>
  <p class="member-bio abs" style="left:547px;top:1738px;width:542px">Sed ut perspiciatis unde omnis iste natus error sit voluptatem accusan tium doloremque laudantium, totam rem aperiam, eaque ipsa quae ab illo inventore veritatis et quasi architecto beatae vitae dicta sunt modi tempora incidunt ut labore et dolore magnam aliquam quaerat volup tate &nbsp;im ad minima veniam, quis nostrum exercitationem ullam corporis suscipit laboriosam, nisi ut aliquid ex ea commodi consequat is autem vel eum iure reprehenderiexplicabo volup tate velit esse quam nihil molestiae consequa.</p>
  <div class="contact-line abs" style="left:547px;top:1964px"><svg width="15" height="15" viewBox="0 0 24 24"><path fill="#12b3bf" d="M6.6 10.8a15 15 0 0 0 6.6 6.6l2.2-2.2a1 1 0 0 1 1-.25 11.4 11.4 0 0 0 3.6.57 1 1 0 0 1 1 1V20a1 1 0 0 1-1 1A17 17 0 0 1 3 4a1 1 0 0 1 1-1h3.5a1 1 0 0 1 1 1c0 1.25.2 2.45.57 3.57a1 1 0 0 1-.25 1z"/></svg>1 888 888 8888</div>
  <div class="contact-line abs" style="left:547px;top:1999px"><svg width="17" height="13" viewBox="0 0 17 13"><rect width="17" height="13" rx="1.5" fill="#12b3bf"/><path d="M1 1.5l7.5 6 7.5-6" stroke="#fff" stroke-width="1.5" fill="none"/></svg>camille@brightvale.coop</div>

  <h3 class="member-name abs" style="left:108px;top:2118px">Jessica</h3>
  <p class="member-bio abs" style="left:110px;top:2183px;width:545px">Sed ut perspiciatis unde omnis iste natus error sit voluptatem accusan tium doloremque laudantium, totam rem aperiam, eaque ipsa quae ab illo inventore veritatis et quasi architecto beatae vitae dicta sunt modi tempora incidunt ut labore et dolore magnam aliquam quaerat volup tate &nbsp;im ad minima veniam, quis nostrum exercitationem ullam corporis suscipit laboriosam, nisi ut aliquid ex ea commodi consequat is autem vel eum iure reprehenderiexplicabo volup tate velit esse quam nihil molestiae consequa.</p>
  <div class="portrait abs" style="left:717px;top:2128px"><div class="portrait-inner"><div class="portrait-img" role="img" aria-label="Portrait of Jessica"></div></div></div>
</section>

<section class="testimonials abs">
  <h2 class="testimonials-title abs">CLIENT TESTIMONIALS</h2>
  <svg class="abs" style="left:66px;top:200px" width="18" height="30" viewBox="0 0 18 30"><path d="M15 3L4 15l11 12" stroke="#fff" stroke-width="3" fill="none"/></svg>
  <div class="client abs" style="left:110px"><span class="dot"></span>Swifta</div>
  <div class="client abs" style="left:310px"><span class="dot"></span>Swifta</div>
  <div class="client active abs" style="left:508px">Novel</div>
  <div class="client abs" style="left:707px"><span class="dot"></span>Swifta</div>
  <div class="client abs" style="left:906px"><span class="dot"></span>Swifta</div>
  <svg class="abs" style="left:1104px;top:200px" width="18" height="30" viewBox="0 0 18 30"><path d="M3 3l11 12L3 27" stroke="#fff" stroke-width="3" fill="none"/></svg>
  <div class="rule abs"></div>
  <div class="avatar abs" role="img" aria-label="Portrait of the client CEO"></div>
  <div class="author abs">John Doe<br>CEO</div>
  <p class="quote abs">“Nam libero tempore, cum soluta nobis est eligendi opticum que nihil impedit quo minus id quod maxime placeat facere possimus, omnis voluptas assumenda est, omnis dolor rep ellendu autem quibusdam et aut .”</p>
</section>

<footer class="site-footer">
  <div class="brand abs"><span class="brand-mark"></span>BRIGHTVALE</div>
  <div class="foot-col abs" style="left:468px;top:3146px">
    <h4>Information</h4>
    <ul><li>About us</li><li>Team</li><li>Jobs</li><li>Hurry</li><li>Freelancing news</li><li>Data protection</li><li>Help</li><li>Sitemap</li></ul>
  </div>
  <div class="foot-col abs" style="left:674px;top:3146px">
    <h4>Quick Links</h4>
    <ul><li>Offers and prices</li><li>Company</li><li>Open Brightvale coop</li><li>Insights</li><li>Create my Profile</li></ul>
  </div>
  <div class="foot-col find abs" style="left:880px;top:3146px">
    <h4>Find Us</h4>
    <ul>
      <li><svg width="11" height="15" viewBox="0 0 11 15" style="margin-top:6px"><path d="M5.5 0A5.5 5.5 0 0 0 0 5.5C0 9.6 5.5 15 5.5 15S11 9.6 11 5.5A5.5 5.5 0 0 0 5.5 0zm0 7.5a2 2 0 1 1 0-4 2 2 0 0 1 0 4z" fill="#12b3bf"/></svg><span>24 Rue des Lilas<br>75011 Paris</span></li>
      <li style="margin-top:27px"><svg width="14" height="14" viewBox="0 0 24 24" style="margin-top:6px"><path fill="#12b3bf" d="M6.6 10.8a15 15 0 0 0 6.6 6.6l2.2-2.2a1 1 0 0 1 1-.25 11.4 11.4 0 0 0 3.6.57 1 1 0 0 1 1 1V20a1 1 0 0 1-1 1A17 17 0 0 1 3 4a1 1 0 0 1 1-1h3.5a1 1 0 0 1 1 1c0 1.25.2 2.45.57 3.57a1 1 0 0 1-.25 1z"/></svg>01 45 67 20 13</li>
      <li style="margin-top:27px"><svg width="17" height="13" viewBox="0 0 17 13" style="margin-top:7px"><rect width="17" height="13" rx="1.5" fill="#12b3bf"/><path d="M1 1.5l7.5 6 7.5-6" stroke="#fff" stroke-width="1.5" fill="none"/></svg>contact@brightvale.coop</li>
    </ul>
  </div>
  <div class="foot-rule abs"></div>
  <p class="copyright abs">© 2020, brightvale.coop.</p>
  <a class="social abs" style="left:945px" aria-label="Social network 1"><span></span></a>
  <a class="social abs" style="left:992px" aria-label="Social network 2"><span></span></a>
  <a class="social abs" style="left:1044px" aria-label="Social network 3"><span></span></a>
</footer>

</body>
</html>
```